Software Development Consulting Company Needs Business Card Design

We need a new business card design for our consultants at Kestrel Works (kestrelworks.example). We are a small firm that provides high-end software development and methodology consulting to medium to large enterprise IT organizations.

Our logo uses Futura for the font and we would like to stick with navy blue and canary yellow for the logo colors. Attached are normal and reversed versions of our logos in illustrator format.
Updates

Hi Everyone, Thank yo very much for your amazing design ideas. I have created a poll for this project and our employees will be voting on the design they wish to use. We will be making a decision this Wednesday (October 22nd). Thanks again, Dale Hartwick

Industry/Entity Type

Business

```html
<!DOCTYPE html>
<html lang="en">
<head>
<meta charset="utf-8">
<title>Kestrel Works — Business Card</title>
<link rel="stylesheet" href="https://fonts.googleapis.com/css2?family=Jost:wght@400;500;600&display=swap">
<style>
  :root {
    --navy: #1b4a6f;
    --canary: #fff200;
    --paper: #ffffff;
    --ink-grey: #555a60;
    --backdrop: #e9e9ee;
  }
  html, body {
    margin: 0;
    width: 1200px;
    height: 980px;
    overflow: hidden;
    background: var(--backdrop);
    font-family: "Jost", sans-serif;
  }
  .sheet {
    position: relative;
    width: 1200px;
    height: 980px;
  }
  .card {
    position: absolute;
    left: 290px;
    width: 620px;
    height: 354px;
    border-radius: 26px;
    overflow: hidden;
    box-shadow: 0 10px 26px rgba(0,0,0,0.14);
  }
  /* Front */
  .card--front { top: 100px; background: var(--paper); }
  .brand {
    position: absolute;
    left: 40px;
    top: 36px;
    display: flex;
    align-items: center;
    gap: 12px;
    color: var(--navy);
    font-weight: 500;
    font-size: 30px;
    letter-spacing: 0.12em;
    text-transform: uppercase;
  }
  .brand__dot {
    width: 22px;
    height: 22px;
    border: 4px solid var(--navy);
    border-radius: 50%;
    box-sizing: border-box;
  }
  .contact {
    position: absolute;
    left: 40px;
    top: 128px;
    margin: 0;
    padding: 0;
    list-style: none;
    color: var(--ink-grey);
    font-size: 17px;
    line-height: 28px;
  }
  .contact li { display: flex; align-items: center; gap: 10px; }
  .contact svg { width: 16px; height: 16px; fill: var(--ink-grey); }
  .person {
    position: absolute;
    right: 44px;
    top: 196px;
    text-align: right;
  }
  .person__name {
    margin: 0;
    color: var(--navy);
    font-weight: 600;
    font-size: 26px;
  }
  .person__title {
    margin: 2px 0 0;
    color: var(--ink-grey);
    font-size: 18px;
  }
  .band {
    position: absolute;
    left: 0;
    right: 0;
    bottom: 0;
    height: 58px;
    background: var(--navy);
    border-top: 3px solid var(--canary);
    box-shadow: 0 -4px 0 var(--paper);
    display: flex;
    align-items: center;
    padding-left: 40px;
    color: var(--paper);
    font-size: 18px;
  }
  /* Back */
  .card--back { top: 520px; background: var(--canary); }
  .back__brand {
    position: absolute;
    left: 0;
    right: 0;
    top: 120px;
    display: flex;
    justify-content: center;
    align-items: center;
    gap: 16px;
    color: var(--navy);
    font-weight: 500;
    font-size: 42px;
    letter-spacing: 0.12em;
    text-transform: uppercase;
  }
  .back__brand .brand__dot { width: 30px; height: 30px; border-width: 5px; }
  .back__url {
    position: absolute;
    left: 0;
    right: 0;
    top: 220px;
    text-align: center;
    color: var(--ink-grey);
    font-size: 20px;
    letter-spacing: 0.3em;
  }
</style>
</head>
<body>
<main class="sheet">
  <section class="card card--front" aria-label="Business card front">
    <div class="brand"><span class="brand__dot"></span>Kestrel Works</div>
    <ul class="contact">
      <li>
        <svg viewBox="0 0 16 16" aria-hidden="true"><path d="M3.5 1.5l2.5 3-1.4 1.6a8 8 0 0 0 5.3 5.3l1.6-1.4 3 2.5-1.6 2A11 11 0 0 1 1.5 3.1z"/></svg>
        012-345-6789
      </li>
      <li>
        <svg viewBox="0 0 16 16" aria-hidden="true"><path d="M1 3h14v10H1zm1.5 1.3V5l5.5 4 5.5-4v-.7z"/></svg>
        info@kestrelworks.example
      </li>
      <li>
        <svg viewBox="0 0 16 16" aria-hidden="true"><path d="M8 1a7 7 0 1 0 0 14A7 7 0 0 0 8 1zm0 1.5c.9 1 1.5 2.6 1.7 4.5H6.3C6.5 5.1 7.1 3.5 8 2.5zM6.3 9h3.4c-.2 1.9-.8 3.5-1.7 4.5-.9-1-1.5-2.6-1.7-4.5zM2.6 7a5.5 5.5 0 0 1 2.7-3.8A9 9 0 0 0 4.3 7zm0 2h1.7a9 9 0 0 0 1 3.8A5.5 5.5 0 0 1 2.6 9zm9.1 0h1.7a5.5 5.5 0 0 1-2.7 3.8 9 9 0 0 0 1-3.8zm0-2a9 9 0 0 0-1-3.8A5.5 5.5 0 0 1 13.4 7z"/></svg>
        www.kestrelworks.example
      </li>
    </ul>
    <div class="person">
      <p class="person__name">Your Name</p>
      <p class="person__title">Title</p>
    </div>
    <div class="band">Harbor City + Fairhaven, IL</div>
  </section>

  <section class="card card--back" aria-label="Business card back">
    <div class="back__brand"><span class="brand__dot"></span>Kestrel Works</div>
    <div class="back__url">www.kestrelworks.example</div>
  </section>
</main>
</body>
</html>
```